Landing Page and Logo for Auto-Blogging Platform

I created a platform that allows users to start a blog for their business, hobby, charity, etc. I need a landing page where users can learn about the platform, benefits of consistent blogging, SEO value, plans/pricing, etc. The landing page needs to have multiple call to action buttons encouraging the visitor to register/sign up for a free trial.

In addition to the landing page, I need a page for users to establish the settings for their blog. This page should be a fairly simple form, intended for the user to enter a few details to set up their blog:
1. Name of Blog
2. Up to 10 topics and/or keywords the blog should focus on
3. Theme: Color-scheme and logo upload for blog.

I have attached the specifications of the platform's functionality so you can better understand how it works, plans/pricing, etc.

I also need a logo for the business. The name of the platform is PostNook.

Target Market(s)

Website owners, bloggers, business owners

Industry/Entity Type

Technology, Internet, web design

Coding

Coded - Design and coding required

Number of Pages Required

2 page

Colors
0054AA
0677BA
7BADD7
CADEEF
E8F1F8
0094D4
00A9DD
6FCCEA
C7EBF8
E9F6FB

Requirements
Must have
• Eye-catching design but fairly light on content (keep it simple and brief.)
Nice to have
• Eye-catching yet simple design, clean and easy to understand what we are offering.
Should not have
• Too much “wordy” and confusing content.

```html
<!DOCTYPE html>
<html lang="en">
<head>
<meta charset="utf-8">
<title>PostNook – Automate Your Blog Posting with AI</title>
<link href="https://fonts.googleapis.com/css2?family=Lato:wght@400;700;900&display=swap" rel="stylesheet">
<style>
:root{
  --blue:#0a78bd;
  --blue-dark:#0054aa;
  --green:#a9c923;
  --green-light:#c2d95a;
  --ink:#2f2f2f;
  --muted:#4a4a4a;
  --line:#dfe6ee;
  --footer:#3d3d3f;
  --white:#fff;
}
*{box-sizing:border-box;margin:0;padding:0}
html,body{width:1200px;height:4097px;overflow:hidden}
body{font-family:'Lato',sans-serif;color:var(--ink);background:var(--white);position:relative}
.abs{position:absolute}
.accent{color:var(--blue);font-weight:700}
.btn{position:absolute;background:var(--green);color:var(--white);font-weight:700;font-size:15px;display:flex;align-items:center;justify-content:center;border-radius:2px}

/* header / hero */
.hero{position:absolute;left:0;top:0;width:1200px;height:748px;background:linear-gradient(90deg,#fff 0%,#fff 40%,#eef1ec 60%,#d9ddd6 100%);box-shadow:0 4px 10px rgba(0,0,0,.06)}
.hero-photo{position:absolute;left:560px;top:0;width:640px;height:748px;background:radial-gradient(ellipse at 55% 55%,#b8bcb9 0%,#d6dad4 45%,rgba(238,241,236,0) 75%)}
.brand{left:111px;top:150px;font-size:48px;font-weight:700;color:#3b3b3b}
.brand-mark{left:145px;top:40px;width:80px;height:80px;border-radius:50%;background:var(--green)}
.nav{left:460px;top:56px;display:flex;gap:36px;font-size:15px;align-items:center}
.nav .active{background:var(--blue);color:#fff;padding:8px 10px;border-radius:2px;font-weight:700}
.search{left:1058px;top:60px}
.hero-kicker{left:111px;top:272px;font-size:33px;color:#333}
.hero-title{left:107px;top:322px;font-size:66px;line-height:70px;font-weight:700;color:var(--blue)}
.hero-text{left:112px;top:484px;width:455px;font-size:14.5px;line-height:23px;color:#333}

/* pricing */
.section-title{position:absolute;width:1200px;text-align:center;font-size:42px;color:#333}
.card{position:absolute;background:#fff;border:1px solid var(--line);border-radius:6px}
.card.featured{box-shadow:0 0 24px rgba(10,120,189,.25);border-color:#c9dbeb;z-index:2}
.badge{position:absolute;border-radius:50%;color:#fff;display:flex;flex-direction:column;align-items:center;justify-content:center;text-align:center;outline-offset:-6px}
.badge.blue{background:var(--blue);outline:2px dashed #fff}
.badge.green{background:var(--green);outline:2px dashed #fff}
.badge .name{font-size:14px}
.badge .price{font-size:28px;font-weight:900;line-height:1.1}
.badge .per{font-size:13px}
.plan-head{position:absolute;width:100%;text-align:center;font-size:25px;line-height:32px;color:#333}
.features{position:absolute;list-style:none}
.features li{display:flex;gap:8px;font-size:12.5px;line-height:17px;color:#444;padding:12px 0;border-bottom:1px solid #e6e6e6}
.features li:last-child{border-bottom:none}
.tick{flex:0 0 16px;height:16px;border-radius:50%;background:var(--blue);display:flex;align-items:center;justify-content:center;margin-top:1px}

/* about */
.about-art{left:111px;top:1655px;width:520px;height:521px;border-radius:0 0 0 260px;background:radial-gradient(circle at 45% 60%,#8fb2cf 0%,#b0c9de 35%,var(--green) 36%,var(--green) 60%,rgba(255,255,255,0) 61%)}
.h2{position:absolute;font-size:44px;color:#333}
.body-text{position:absolute;font-size:14.5px;line-height:23px;color:#444}

/* steps */
.step{position:absolute;width:86px;height:86px;border-radius:50%;background:#d9d9d9;color:#444;font-size:46px;font-weight:700;display:flex;align-items:center;justify-content:center}
.step.on{background:var(--green);color:#fff}
.step-line{left:267px;top:2383px;width:666px;height:4px;background:#d9d9d9}
.step-panel{left:236px;top:2500px;width:727px;height:191px;border-radius:6px;background:linear-gradient(120deg,#c4da5c,#b7d23d);color:#fff;font-size:26px;font-weight:700;text-align:center;line-height:50px;padding-top:44px;padding-left:80px}
.step-person{left:215px;top:2460px;width:130px;height:231px;border-radius:60px 60px 0 0;background:linear-gradient(180deg,#c79c82,#e9e6e2)}

/* methods */
.footer{left:0;top:3697px;width:1200px;height:400px;background:var(--footer)}
.methods{left:111px;top:3392px;width:978px;height:377px;background:var(--blue);border-radius:16px}
.methods-title{left:0;top:62px;width:978px;text-align:center;font-size:44px;color:#fff}
.methods-title b{color:var(--green)}
.m-num{position:absolute;width:66px;height:66px;border-radius:50%;border:3px solid #fff;color:#fff;font-size:27px;font-weight:700;display:flex;align-items:center;justify-content:center}
.m-text{position:absolute;color:#fff;font-size:15px;line-height:23px}
.m-card{left:333px;top:141px;width:306px;height:175px;background:#fff;border-radius:4px;text-align:center}
.m-card .m-num{border-color:var(--green);color:var(--green);width:54px;height:54px;font-size:22px;left:126px;top:18px}
.m-card p{position:absolute;left:22px;top:88px;width:262px;font-size:14px;line-height:19px;color:#333}

.foot-brand{left:0;top:3842px;width:1200px;text-align:center;font-size:56px;font-weight:700;color:#fff}
.foot-nav{left:0;top:3929px;width:1200px;display:flex;justify-content:center;gap:36px;color:#fff;font-size:15px}
.social{left:538px;top:3978px;display:flex;gap:18px}
.social span{width:30px;height:30px;border-radius:4px;background:#fff}
.social span:first-child{background:var(--green)}
.copy{left:0;top:4070px;width:1200px;text-align:center;color:#fff;font-size:12.5px}
.ph{position:absolute}
</style>
</head>
<body>

<header class="hero">
  <div class="hero-photo" role="img" aria-label="Photo of a laptop on a desk showing a blog page"></div>
  <div class="abs brand-mark" aria-hidden="true"></div>
  <div class="abs brand">PostNook</div>
  <nav class="abs nav">
    <span class="active">Home</span><span>About Us</span><span>Pricing</span><span>Benefits</span><span>SEO Value</span><span>Contact Us</span>
  </nav>
  <svg class="abs search" width="26" height="26" viewBox="0 0 26 26" aria-label="Search"><circle cx="11" cy="11" r="8" fill="none" stroke="#222" stroke-width="2.4"/><line x1="17" y1="17" x2="24" y2="24" stroke="#222" stroke-width="2.4"/></svg>
  <div class="abs hero-kicker">Automate Your</div>
  <h1 class="abs hero-title">Blog Posting<br>with AI</h1>
  <p class="abs hero-text">Transform your blogging experience with our AI-powered platform that not only generates and optimizes content tailored to your audience but also continuously learns and adapts to deliver smarter insights, ensuring your voice stands out in a crowded digital landscape.</p>
  <div class="btn" style="left:112px;top:626px;width:138px;height:37px">Get Started</div>
</header>

<!-- Pricing -->
<h2 class="section-title" style="top:828px">Our <span class="accent">Pricing</span></h2>

<div class="card" style="left:111px;top:1026px;width:306px;height:502px">
  <div class="plan-head" style="top:82px">1 blog post (up to 2,000<br>words) every month:</div>
  <ul class="features" style="left:35px;top:174px;width:245px">
    <li><span class="tick"><svg width="9" height="9" viewBox="0 0 10 10"><path d="M1.5 5l2.5 2.5 4.5-5" stroke="#fff" stroke-width="1.8" fill="none"/></svg></span>Excepteur sint occaecat cupidatat non proident, mollit anim id est laborum.</li>
    <li><span class="tick"><svg width="9" height="9" viewBox="0 0 10 10"><path d="M1.5 5l2.5 2.5 4.5-5" stroke="#fff" stroke-width="1.8" fill="none"/></svg></span>Excepteur sint occaecat cupidatat non proident, mollit anim id est laborum.</li>
    <li><span class="tick"><svg width="9" height="9" viewBox="0 0 10 10"><path d="M1.5 5l2.5 2.5 4.5-5" stroke="#fff" stroke-width="1.8" fill="none"/></svg></span>Excepteur sint occaecat cupidatat non proident, mollit anim id est laborum.</li>
    <li><span class="tick"><svg width="9" height="9" viewBox="0 0 10 10"><path d="M1.5 5l2.5 2.5 4.5-5" stroke="#fff" stroke-width="1.8" fill="none"/></svg></span>Excepteur sint occaecat cupidatat</li>
  </ul>
  <div class="btn" style="left:93px;top:435px;width:134px;height:32px;font-size:13px">Get A Proposal</div>
</div>

<div class="card" style="left:786px;top:1026px;width:303px;height:502px">
  <div class="plan-head" style="top:82px">1 blog post (up to 2,000<br>words) every week:</div>
  <ul class="features" style="left:22px;top:174px;width:245px">
    <li><span class="tick"><svg width="9" height="9" viewBox="0 0 10 10"><path d="M1.5 5l2.5 2.5 4.5-5" stroke="#fff" stroke-width="1.8" fill="none"/></svg></span>Excepteur sint occaecat cupidatat non proident, mollit anim id est laborum.</li>
    <li><span class="tick"><svg width="9" height="9" viewBox="0 0 10 10"><path d="M1.5 5l2.5 2.5 4.5-5" stroke="#fff" stroke-width="1.8" fill="none"/></svg></span>Excepteur sint occaecat cupidatat non proident, mollit anim id est laborum.</li>
    <li><span class="tick"><svg width="9" height="9" viewBox="0 0 10 10"><path d="M1.5 5l2.5 2.5 4.5-5" stroke="#fff" stroke-width="1.8" fill="none"/></svg></span>Excepteur sint occaecat cupidatat non proident, mollit anim id est laborum.</li>
    <li><span class="tick"><svg width="9" height="9" viewBox="0 0 10 10"><path d="M1.5 5l2.5 2.5 4.5-5" stroke="#fff" stroke-width="1.8" fill="none"/></svg></span>Excepteur sint occaecat cupidatat</li>
  </ul>
  <div class="btn" style="left:80px;top:435px;width:134px;height:32px;font-size:13px">Get A Proposal</div>
</div>

<div class="card featured" style="left:415px;top:992px;width:372px;height:576px">
  <div class="plan-head" style="top:96px">1 blog post (up to 3,000<br>words) per day plus<br>unlimited manual posting:</div>
  <ul class="features" style="left:40px;top:220px;width:292px">
    <li style="font-size:13.5px;line-height:20px;padding:14px 0"><span class="tick"><svg width="9" height="9" viewBox="0 0 10 10"><path d="M1.5 5l2.5 2.5 4.5-5" stroke="#fff" stroke-width="1.8" fill="none"/></svg></span>Excepteur sint occaecat cupidatat non proident, mollit anim id est laborum.</li>
    <li style="font-size:13.5px;line-height:20px;padding:14px 0"><span class="tick"><svg width="9" height="9" viewBox="0 0 10 10"><path d="M1.5 5l2.5 2.5 4.5-5" stroke="#fff" stroke-width="1.8" fill="none"/></svg></span>Excepteur sint occaecat cupidatat non proident, mollit anim id est laborum.</li>
    <li style="font-size:13.5px;line-height:20px;padding:14px 0"><span class="tick"><svg width="9" height="9" viewBox="0 0 10 10"><path d="M1.5 5l2.5 2.5 4.5-5" stroke="#fff" stroke-width="1.8" fill="none"/></svg></span>Excepteur sint occaecat cupidatat non proident, mollit anim id est laborum.</li>
    <li style="font-size:13.5px;line-height:20px;padding:14px 0"><span class="tick"><svg width="9" height="9" viewBox="0 0 10 10"><path d="M1.5 5l2.5 2.5 4.5-5" stroke="#fff" stroke-width="1.8" fill="none"/></svg></span>Excepteur sint occaecat cupidatat</li>
  </ul>
  <div class="btn" style="left:110px;top:500px;width:154px;height:36px">Get A Proposal</div>
</div>

<div class="badge blue" style="left:215px;top:960px;width:128px;height:128px"><span class="name">Base Plan</span><span class="price">$9.99</span><span class="per">/mo.</span></div>
<div class="badge green" style="left:529px;top:917px;width:146px;height:146px;z-index:3"><span class="name" style="font-size:15px">Ultimate Plan</span><span class="price" style="font-size:31px">$24.99</span><span class="per">/mo.</span></div>
<div class="badge blue" style="left:868px;top:960px;width:128px;height:128px"><span class="name">Premium Plan</span><span class="price">$14.99</span><span class="per">/mo.</span></div>

<!-- About -->
<div class="ph about-art" role="img" aria-label="Smiling woman in a denim shirt beside dashboard screenshots, on a green circle"></div>
<h2 class="h2" style="left:705px;top:1672px">About The <span class="accent">Platform</span></h2>
<p class="body-text" style="left:702px;top:1750px;width:390px">There needs to be a super-admin panel where platform owner/administrator can see users, their activity, manage user access, etc. Each user will have a dashboard where they control their settings such as account information, billing, view blog posts, view blog post topics, etc. From this dashboard, the user can customize the “look and feel” of their blog including theme, hero banner, header, footer, logo, color scheme, etc.<br><br>The platform will require a list of blog topics. Based on the topics list, the software will need to automatically send prompts to TextMind in the specified intervals (monthly, weekly, or daily), receive the blog content, and post it to the blog.</p>
<div class="btn" style="left:702px;top:2109px;width:137px;height:38px">Read More</div>

<!-- Steps -->
<h2 class="section-title" style="top:2252px">How to Set Up <span class="accent">the Auto-Blog</span></h2>
<div class="abs step-line"></div>
<div class="step on" style="left:224px;top:2341px">01</div>
<div class="step" style="left:439px;top:2341px">02</div>
<div class="step" style="left:665px;top:2341px">03</div>
<div class="step" style="left:890px;top:2341px">04</div>
<div class="abs step-panel">Select frequency of Automated Blog Posts<br>(Daily, Weekly, or Monthly)</div>
<div class="ph step-person" role="img" aria-label="Woman in a white blouse pointing at the step text"></div>

<!-- SEO -->
<h2 class="h2" style="left:111px;top:2805px">SEO <span class="accent">Value</span></h2>
<p class="body-text" style="left:111px;top:2884px;width:390px">Lorem ipsum dolor sit amet, consectetur adipiscing elit, sed do eiusmod tempor incididunt ut labore et dolore magna aliqua. Ut enim ad minim veniam, quis nostrud exercitation ullamco laboris nisi ut aliquip ex ea commodo consequat. Duis aute irure dolor in reprehenderit in voluptate velit esse cillum dolore eu fugiat nulla pariatur.<br><br>Sed ut perspiciatis unde omnis iste natus error sit voluptatem accusantium doloremque laudantium, totam rem aperiam, eaque ipsa quae ab illo inventore veritatis et quasi architecto beatae vitae dicta sunt explicabo. Nemo enim ipsam voluptatem quia voluptas sit aspernatur aut odit aut fugit, sed quia consequuntur magni dolores eos qui ratione voluptatem sequi nesciunt.</p>
<div class="btn" style="left:111px;top:3247px;width:137px;height:37px">Read More</div>
<div class="ph" style="left:565px;top:2785px;width:557px;height:533px;border-radius:50% 50% 50% 12%;background:radial-gradient(circle at 45% 45%,#6f7480 0%,#a7acb6 40%,#dfe3ea 70%,rgba(255,255,255,0) 72%)" role="img" aria-label="Hands typing on a laptop showing a blog screen, with dashboard screenshots"></div>

<!-- Methods & footer -->
<footer class="abs footer"></footer>
<section class="abs methods">
  <h2 class="abs methods-title">Methods To <b>Create Blog Topics</b></h2>
  <div class="m-num" style="left:28px;top:199px">01</div>
  <p class="m-text" style="left:114px;top:206px;width:190px">The user enters them into a table manually</p>
  <div class="abs m-card">
    <div class="m-num">02</div>
    <p>AI can create the list of blog topics based on a prompt such as: “Provide a list of 52 blog topics for a handyman business’s blog.</p>
  </div>
  <div class="m-num" style="left:685px;top:199px">03</div>
  <p class="m-text" style="left:773px;top:206px;width:190px">The user uploads a list of blog topics in CSV format.</p>
</section>

<div class="abs foot-brand">PostNook</div>
<nav class="abs foot-nav"><span>Home</span><span>About Us</span><span>Pricing</span><span>Benefits</span><span>SEO Value</span><span>Contact Us</span></nav>
<div class="abs social" aria-label="Social links"><span></span><span></span><span></span></div>
<div class="abs copy">Copyright © 2024 PostNook. All rights reserved.</div>

</body>
</html>
```